Book Title: “Faith: Road of Endless Grace” Please see the attachment “Text on the cover”.

Book Cover Design Instructions: This book is meant for people of all religions and nationalities. Therefore, on the cover, there should be no mosque or an object specific to any religion. The primary emphasis should be on the "unconditional love of God." Therefore, use universal symbols of love. The second priority themes could be Sufism, Peace, and self-improvement. Rest is your imagination. Please also see the attachment: 'Book description and author's Bio.'
This book has the potential to be a best seller. Please do a good job.
What Book Cover Formats are required: A designer should submit cover designs in three formats: (1) eBook, (2) Paperback, and (3) Hardback. These books will be published on Borvex QPL.
Format requirements for eBooks are available from: https://qpl.borvex.example/en_US/help/topic/R731928457.
You can find paperback and hardback cover measurements from: https://qpl.borvex.example/en_US/cover-calculator
• To complete the project, all three formats should be accepted by Borvex QPL.
• The book interior trim size is 6.14 X 9.21 inches.
• Interior Type: Premium color.
• No bleed.
• I do not upload barcode. So, the back cover should have room for Borvex to print the barcode.
• Number of pages 126.
Compensation for the designer: After selecting one designer, I will increase the amount by $200 on Artvelle to compensate for three deliverables.
Follow-up of the Project:
After the book is published, I may need minor revisions. For example, the number of pages may change. Therefore, I will need the same design in revised sizes. In that case, I will pay $25 for each revision. For example, if the number of pages changes, I will need a different spine for paperback and hardback, then I will pay the artist $25 + $25 = $50 for both designs.
List of Enclosers:
1. Text on the cover.
2. Book description and author's Bio for the back cover.
3. Later, I will upload my picture for the book's back cover.

Target Market(s)

Any adult

Industry/Entity Type

Any industry

Requirements
Must have
• Three Deliverables

```html
<!DOCTYPE html>
<html lang="en">
<head>
<meta charset="utf-8">
<title>Faith: Road of Endless Grace – Wraparound Cover</title>
<link href="https://fonts.googleapis.com/css2?family=Marcellus&family=Marcellus+SC&family=Cormorant+SC:wght@600&family=Montserrat:wght@400&display=swap" rel="stylesheet">
<style>
  :root{
    --page:#ffffff;
    --navy:#121540;
    --ink:#ffffff;
    --title-ink:#141a4f;
    --sky-top:#8b93d6;
    --sky-mid:#d9c3ea;
    --glow:#fff7c8;
    --cloud:#c6b8ec;
    --cloud-blue:#7e9ae0;
    --box:#ffffff;
  }
  *{margin:0;padding:0;box-sizing:border-box}
  html,body{width:1200px;height:1200px;overflow:hidden;background:var(--page)}
  .canvas{position:relative;width:1200px;height:1200px}
  .cover{position:absolute;left:51px;top:207px;width:1105px;height:793px;background:var(--navy);box-shadow:0 1px 3px rgba(0,0,0,.25)}
  .back{position:absolute;left:33px;top:0;width:480px;height:100%;color:var(--ink)}
  .back-title{position:absolute;left:0;top:33px;font-family:"Marcellus SC",serif;font-weight:400;font-size:27px;letter-spacing:1.6px;white-space:nowrap}
  .back-subtitle{position:absolute;left:1px;top:80px;font-family:"Marcellus SC",serif;font-weight:400;font-size:14px;letter-spacing:.7px;white-space:nowrap}
  .blurb{position:absolute;left:1px;top:104px;width:465px;font-family:"Montserrat",sans-serif;font-size:10.4px;letter-spacing:.15px;line-height:13px;text-align:justify}
  .blurb p{margin-bottom:12.5px}
  .author-photo{position:absolute;left:1px;top:547px;width:134px;height:168px;background:var(--box)}
  .bio{position:absolute;left:151px;top:551px;width:315px;font-family:"Montserrat",sans-serif;font-size:10.4px;letter-spacing:.15px;line-height:13px;text-align:justify}
  .bio h3{font-family:"Marcellus",serif;font-weight:400;font-size:17px;letter-spacing:.8px;margin-bottom:6px;text-align:left}
  .barcode-area{position:absolute;left:306px;top:656px;width:192px;height:103px;background:var(--box)}
  .spine{position:absolute;left:521px;top:0;width:52px;height:100%;writing-mode:vertical-rl;display:flex;flex-direction:row;align-items:center;color:var(--ink);font-family:"Marcellus",serif;font-size:22px;letter-spacing:1.4px;padding-top:38px}
  .spine span{white-space:nowrap}
  .spine .spine-author{margin-top:68px}
  .front{position:absolute;left:573px;top:0;width:532px;height:100%}
  .front-art{position:absolute;left:0;top:0;width:532px;height:712px;
    background:
      radial-gradient(circle at 52% 37%, var(--glow) 0, #fff3b0 14%, rgba(255,240,200,.55) 24%, rgba(255,230,220,0) 42%),
      radial-gradient(ellipse at 15% 95%, var(--cloud-blue) 0, rgba(126,154,224,0) 40%),
      radial-gradient(ellipse at 90% 80%, var(--cloud-blue) 0, rgba(126,154,224,0) 35%),
      linear-gradient(180deg, var(--sky-top) 0%, #b7b6e6 22%, var(--sky-mid) 45%, #e6cde6 60%, var(--cloud) 85%, #b9b2e8 100%)}
  .front-title{position:absolute;left:0;top:0;width:100%;text-align:center;font-family:"Marcellus",serif;font-weight:400;color:var(--title-ink);line-height:1;text-shadow:0 0 3px rgba(255,255,255,.8)}
  .front-title span{position:absolute;left:0;width:100%;white-space:nowrap}
  .front-title .l1{top:404px;font-size:96px;letter-spacing:3px}
  .front-title .l2{top:490px;font-size:64px}
  .front-title .l3{top:546px;font-size:56px;letter-spacing:1px}
  .front-subtitle{position:absolute;left:0;width:100%;top:620px;text-align:center;font-family:"Cormorant SC",serif;font-weight:600;font-style:italic;font-size:27px;line-height:31px;color:var(--title-ink);text-shadow:0 0 3px rgba(255,255,255,.8)}
  .front-author{position:absolute;left:0;width:100%;top:735px;text-align:center;font-family:"Marcellus",serif;font-size:30px;letter-spacing:1.6px;color:var(--ink)}
</style>
</head>
<body>
<div class="canvas">
  <section class="cover">
    <div class="back">
      <h1 class="back-title">FAITH: ROAD OF ENDLESS GRACE</h1>
      <h2 class="back-subtitle">COMPANION TO NURTURING INNER CALM AND GENTLE LIVING</h2>
      <div class="blurb">
        <p>This book weaves together the reflective traditions of mystic poets with timeless teachings on compassion to offer a clear and gentle map for inner growth. Readers are invited to taste for themselves the quiet joy and generous love that seekers have treasured across many cultures. Along the way, it explores these central questions:</p>
        <p>How can a person love the Divine without conditions? This love is the deepest of all, and it opens a steady and life-changing inner journey.</p>
        <p>How to sense the love of the Divine, which can bring lasting calm and gratitude.</p>
        <p>How to accept and love yourself fully, which supports growth and inner balance.</p>
        <p>What is the wisest way to meet life’s hardest moments so that pain eases and healing comes sooner?</p>
        <p>The book also looks closely at the duty to avoid harm, cruelty and unfairness toward others, a theme that appears again and again in sacred writing. Treating every person with justice and kindness should be the first concern of anyone on a spiritual path.</p>
        <p>Love and peace are not only ideals to speak about. History offers many leaders who settled deep conflicts through patience, dialogue and fair agreements rather than force, and who built communities where people of many beliefs lived side by side in trust.</p>
        <p>These stories show that reconciliation is possible even between bitter rivals, and that a calm, principled response can end cycles of hostility that once seemed endless.</p>
        <p>Above all, this book describes a practical method for reaching a settled, grateful and peaceful heart, step by step, the quiet goal shared by every sincere traveler on the inner road.</p>
      </div>
      <div class="author-photo" role="img" aria-label="Space reserved for the author's portrait"></div>
      <div class="bio">
        <h3>DR. RAFIQ MALVANI</h3>
        <p>Dr. Malvani studied astronomy and engineering and spent many years designing software for hospitals. He later earned a doctorate in comparative spirituality and helped start a community center in Oregon.</p>
      </div>
      <div class="barcode-area" aria-label="Space reserved for the printer's barcode"></div>
    </div>

    <div class="spine">
      <span class="spine-title">FAITH: ROAD OF ENDLESS GRACE</span>
      <span class="spine-author">DR. RAFIQ MALVANI</span>
    </div>

    <div class="front">
      <div class="front-art" role="img" aria-label="Illustration of a radiant sun with light rays and stars above soft pastel clouds"></div>
      <h1 class="front-title">
        <span class="l1">FAITH</span>
        <span class="l2">ROAD OF</span>
        <span class="l3">ENDLESS GRACE</span>
      </h1>
      <p class="front-subtitle">Companion to Nurturing Inner<br>Calm and Gentle Living</p>
      <p class="front-author">DR. RAFIQ MALVANI</p>
    </div>
  </section>
</div>
</body>
</html>
```